Fizz's Shed & Grill Burger Restaurant Website - HomePage Only PSD

I need a website design for a restaurant called "Fizz's Shed and Grill" featuring burgers, wings, beer, live music, trivia, and more. I have several images of the restaurant and they already have their logo files created (see attached). I want some type of wood background and integrate the silver tin. This needs to be a modern, hip and fun type design. Design must incorporate these attached graphics.

UPDATE - just added a few more images of things I really like to be incorporated into my designs.
Updates

Industry/Entity Type

Burger Restaurant

Number of Pages Required

1 page

Font styles to use
Sans Serif

Requirements
Must have
• Restaurant/Bar theme with integration of existing logo and the red wood look.
Nice to have
• - Modern Fun appearance
• - Use Pelko Fonts

```html
<!DOCTYPE html>
<html lang="en">
<head>
<meta charset="utf-8">
<title>Fizz's Shed and Grill</title>
<link rel="stylesheet" href="https://fonts.googleapis.com/css2?family=Pacifico&family=Open+Sans:wght@400;600&family=Tinos:wght@400;700&display=swap">
<style>
:root{
  --orange:#e8622a;
  --orange-dark:#c94f1c;
  --paper:#f1f0ee;
  --ink:#1d1d1d;
  --text:#3a3a3a;
  --wood-1:#2a1a12;
  --wood-2:#3d271b;
  --footer:#2b1a12;
  --field:#4a3428;
  --white:#ffffff;
}
*{box-sizing:border-box;margin:0;padding:0}
html,body{width:1200px;height:3536px;overflow:hidden}
body{position:relative;background:var(--paper);font-family:"Tinos",serif;color:var(--text)}
.abs{position:absolute}
.script{font-family:"Pacifico",cursive;color:var(--orange);font-weight:400;line-height:1;white-space:nowrap}
.caps{font-family:"Tinos",serif;color:var(--ink);letter-spacing:1px;text-transform:uppercase;font-weight:400;line-height:1;white-space:nowrap}
.btn{position:absolute;background:var(--orange);color:#fff;font-family:"Open Sans",sans-serif;font-size:13px;display:flex;align-items:center;justify-content:center;border-radius:2px;white-space:nowrap}
.photo{position:absolute}

/* top bar */
.topbar{left:0;top:0;width:1200px;height:28px;background:var(--orange);color:#fff;font-family:"Open Sans",sans-serif;font-size:12px}
.topbar .info{position:absolute;left:492px;top:6px;display:flex;gap:26px;align-items:center}
.topbar .social{position:absolute;left:930px;top:8px;display:flex;gap:7px}
.topbar .social span{width:11px;height:11px;border-radius:50%;background:#fff;opacity:.9}

/* hero */
.hero{left:0;top:28px;width:1200px;height:613px;background:radial-gradient(ellipse at 45% 60%,#a0582c 0%,#6b3518 35%,#2f1a0e 70%,#1a0f08 100%)}
.nav{left:0;top:28px;width:1200px;height:72px;background:rgba(20,12,8,.55)}
.nav-logo{left:130px;top:34px;width:60px;height:60px;border:2px solid #fff;border-radius:50%;color:#fff;font-family:"Open Sans",sans-serif;font-size:9px;display:flex;align-items:center;justify-content:center;text-align:center;line-height:1.2}
.nav-links{left:0;top:0;font-family:"Open Sans",sans-serif;font-size:13px;color:#fff}
.nav-links span{position:absolute;top:55px;white-space:nowrap}
.nav-links .active{color:var(--orange)}
.booking{left:936px;top:46px;width:126px;height:36px}
.hero-logo{left:520px;top:125px;width:160px;height:160px;border:4px solid #fff;border-radius:50%;color:#fff;font-family:"Open Sans",sans-serif;font-weight:600;font-size:17px;display:flex;align-items:center;justify-content:center;text-align:center;line-height:1.25}
.hero-title{left:0;top:318px;width:1200px;text-align:center;font-family:"Pacifico",cursive;color:#fff;font-size:78px;line-height:1;font-weight:400}
.hero-text{left:250px;top:452px;width:700px;text-align:center;color:#fff;font-size:19px;line-height:1.3}
.view-menu{left:536px;top:516px;width:128px;height:36px;border:2px solid #fff;color:#fff;font-family:"Open Sans",sans-serif;font-size:13px;display:flex;align-items:center;justify-content:center}
.dots{left:568px;top:601px;display:flex;gap:9px}
.dots span{width:9px;height:9px;border-radius:50%;background:rgba(255,255,255,.5)}
.dots span:first-child{background:var(--orange)}

/* about */
.about-frame{left:140px;top:748px;width:330px;height:255px;background:#fff;transform:rotate(-3deg);box-shadow:0 4px 14px rgba(0,0,0,.25);padding:12px}
.about-frame .photo{position:static;width:100%;height:100%;background:linear-gradient(180deg,#5fa3d8 0%,#3f7fb8 35%,#b3532d 55%,#8a3a1e 100%)}
.about-script{left:536px;top:734px;font-size:24px}
.about-title{left:532px;top:768px;font-size:30px}
.body-copy{font-size:12px;line-height:1.4;color:var(--text)}
.about-copy{left:536px;top:810px;width:462px}
.about-copy p+p{margin-top:12px}
.read-more{left:532px;top:940px;width:118px;height:36px}
.plate{border-radius:50%;box-shadow:0 6px 14px rgba(0,0,0,.3)}
.plate-salmon{left:980px;top:880px;width:260px;height:200px;background:radial-gradient(circle at 50% 45%,#e07a4a 0%,#c85a36 35%,#f3f0ea 62%,#e4e1dc 100%)}

/* wood */
.wood{left:0;top:1136px;width:1200px;height:627px;background:repeating-linear-gradient(90deg,var(--wood-1) 0 58px,var(--wood-2) 58px 62px,#24160f 62px 122px,#33211a 122px 126px)}
.recipe-card{left:132px;top:1245px;width:425px;height:372px;background:var(--paper);box-shadow:0 4px 14px rgba(0,0,0,.35)}
.recipe-script{left:34px;top:38px;font-size:22px}
.recipe-title{left:32px;top:70px;font-size:28px}
.recipe-copy{left:36px;top:116px;width:355px}
.recipe-copy p+p{margin-top:12px}
.view-details{left:34px;top:292px;width:118px;height:36px}
.steak-frame{left:535px;top:1214px;width:533px;height:440px;background:#fff;padding:8px}
.steak-frame .photo{position:static;width:100%;height:100%;background:radial-gradient(ellipse at 45% 40%,#9a4a22 0%,#6a2c12 40%,#e0781e 65%,#2b140a 100%)}
.plate-burger{left:-110px;top:1632px;width:276px;height:150px;background:radial-gradient(circle at 60% 50%,#d9902f 0%,#b86a1e 38%,#f5f3ef 62%,#e6e3de 100%)}

/* experience */
.exp-script{left:0;top:1838px;width:1200px;text-align:center;font-size:24px}
.exp-title{left:0;top:1872px;width:1200px;text-align:center;font-size:30px}
.tile{position:absolute;width:234px;height:243px}
.t1{left:132px;top:1952px;background:radial-gradient(circle at 50% 50%,#c9832f,#7a3a17 60%,#2a170d)}
.t2{left:366px;top:1952px;background:radial-gradient(circle at 50% 50%,#b0521f,#7a2f10 60%,#2d1a10)}
.t3{left:600px;top:1952px;background:linear-gradient(160deg,#5a3a22,#2a1a10)}
.t4{left:834px;top:1952px;background:radial-gradient(circle at 50% 55%,#8a4a2a,#5a3b28 60%,#3a2a1e)}
.t5{left:132px;top:2240px;background:linear-gradient(180deg,#7a5a38,#c9882e 55%,#6a4a28)}
.t6{left:366px;top:2240px;background:radial-gradient(circle at 50% 50%,#6a3a22,#3a2418 65%,#2a1a12)}
.t7{left:600px;top:2240px;background:radial-gradient(circle at 50% 55%,#a04a28,#6a3a22 60%,#3b2a20)}
.t8{left:834px;top:2240px;background:linear-gradient(180deg,#e0a040,#b86a1e 60%,#7a4212)}
.beer-box{left:640px;top:1985px;width:175px;height:170px;background:rgba(0,0,0,.55);color:#fff;text-align:center;padding-top:28px}
.beer-box h3{font-family:"Tinos",serif;font-weight:400;font-size:15px;line-height:1.3;text-transform:uppercase}
.beer-box .price{font-size:30px;margin-top:12px;line-height:1.1}
.beer-box .btn{left:50px;top:122px;width:76px;height:26px;font-size:11px}
.plate-fries{left:1040px;top:2470px;width:260px;height:250px;background:radial-gradient(circle at 45% 50%,#d9a040 0%,#b8742a 38%,#f5f3ef 62%,#e4e1dc 100%)}

/* testimonials */
.testi{left:0;top:2569px;width:1200px;height:500px;background:linear-gradient(180deg,#c9c6c1 0%,#aeaaa4 45%,#d1cec9 100%)}
.testi-script{left:0;top:2630px;width:1200px;text-align:center;font-size:22px}
.testi-title{left:0;top:2662px;width:1200px;text-align:center;font-size:30px}
.quote{position:absolute;top:2735px;width:296px;height:205px;background:#fff;padding:26px 20px;font-size:15px;line-height:1.3;color:var(--text)}
.avatar{position:absolute;top:2912px;width:92px;height:92px;border-radius:50%;border:4px solid var(--orange);background:radial-gradient(circle at 50% 40%,#c9a48a,#8a6a55 60%,#4a3a30)}
.who{position:absolute;top:2950px;font-size:11px;line-height:1.3;color:#2a2a2a}

/* footer */
.footer{left:0;top:3069px;width:1200px;height:384px;background:var(--footer);color:#fff}
.f-head{position:absolute;top:3118px;font-family:"Pacifico",cursive;font-weight:400;font-size:20px;line-height:1.2;color:#fff;white-space:nowrap}
.f-text{position:absolute;font-size:11px;line-height:1.4;text-align:center;color:#fff}
.f-social{left:170px;top:3338px;display:flex;gap:14px}
.f-social span{width:14px;height:14px;border-radius:50%;background:var(--orange)}
.field{position:absolute;left:772px;width:296px;height:36px;background:var(--field);color:#b9a89c;font-family:"Open Sans",sans-serif;font-size:11px;padding:10px 12px}
.submit{left:772px;top:3388px;width:120px;height:38px}
.copyright{left:0;top:3453px;width:1200px;height:83px;background:var(--orange);color:#fff;font-family:"Open Sans",sans-serif;font-size:11px;display:flex;align-items:center;justify-content:center}
</style>
</head>
<body>

<!-- hero -->
<div class="abs hero photo" role="img" aria-label="Close-up of a grilled burger with fries on a wooden board"></div>
<div class="abs topbar">
  <div class="info">
    <span>
      <svg width="11" height="11" viewBox="0 0 12 12" style="vertical-align:-1px"><circle cx="6" cy="6" r="5" fill="none" stroke="#fff" stroke-width="1.4"/><path d="M6 3v3l2 1.5" stroke="#fff" stroke-width="1.3" fill="none"/></svg>
      Order Foods 24/7
    </span>
    <span>
      <svg width="11" height="11" viewBox="0 0 12 12" style="vertical-align:-1px"><path d="M3 1l2 2.5-1.2 1.4a7 7 0 0 0 3.3 3.3L8.5 7 11 9l-1.3 2C5.5 11 1 6.5 1 2.3z" fill="#fff"/></svg>
      555 0142 8830
    </span>
  </div>
  <div class="social"><span></span><span></span><span></span><span></span><span></span><span></span><span></span></div>
</div>
<div class="abs nav"></div>
<div class="abs nav-logo">Fizz's<br>Shed &amp; Grill</div>
<nav class="abs nav-links">
  <span class="active" style="left:438px">Home</span>
  <span style="left:516px">Menu</span>
  <span style="left:590px">About us</span>
  <span style="left:688px">Delivery</span>
  <span style="left:780px">News</span>
  <span style="left:852px">Features</span>
</nav>
<div class="btn booking">Table Booking</div>

<div class="abs hero-logo">Fizz's<br>Shed and Grill</div>
<h1 class="abs hero-title">Tasty Burgers</h1>
<p class="abs hero-text">Sed ut perspiciatis unde omnis iste natus error sit voluptatem accusantium doloremque laudantium, totam rem aperiam, eaque ipsa quae ab illo inventore veritatis et quasi.</p>
<div class="abs view-menu">View Menu</div>
<div class="abs dots"><span></span><span></span><span></span></div>

<!-- about -->
<div class="abs about-frame"><div class="photo" role="img" aria-label="Restaurant building with red wooden roof against a blue sky"></div></div>
<h2 class="abs script about-script">About us</h2>
<h3 class="abs caps about-title">We are tasty</h3>
<div class="abs body-copy about-copy">
  <p>Lorem Ipsum is simply dummy text of the printing and typesetting industry. Lorem Ipsum has been the industry's standard.</p>
  <p>dard dummy text ever since the 1500s, when an unknown printer took a galley of type and scrambled it to make a type specimen book. It has survived not only five centuries, but also the leap into electronic typesetting, remaining essentially unchanged since the 1500s.</p>
</div>
<div class="btn read-more">Read More</div>
<div class="photo plate plate-salmon" role="img" aria-label="Plate of grilled salmon with lemon and salad"></div>

<!-- special recipes -->
<div class="abs wood" role="img" aria-label="Dark wooden plank background"></div>
<div class="abs recipe-card">
  <h2 class="abs script recipe-script">Special Recipes</h2>
  <h3 class="abs caps recipe-title">Taste of precious</h3>
  <div class="abs body-copy recipe-copy">
    <p>Lorem Ipsum is simply dummy text of the printing and typesetting industry. Lorem Ipsum has been the industry's standard.</p>
    <p>dard dummy text ever since the 1500s, when an unknown printer took a galley of type and scrambled it to make a type specimen book. It has survived not only five centuries, but also the leap into electronic typesetting, remaining essentially unchanged.</p>
  </div>
  <div class="btn view-details">View Details</div>
</div>
<div class="abs steak-frame"><div class="photo" role="img" aria-label="Steak on a flaming grill"></div></div>
<div class="photo plate plate-burger" role="img" aria-label="Burger on a white plate"></div>

<!-- experience -->
<h2 class="abs script exp-script">Delightful</h2>
<h3 class="abs caps exp-title">Experience</h3>
<div class="tile t1" role="img" aria-label="Burger with tomato and lettuce"></div>
<div class="tile t2" role="img" aria-label="Chicken wings with celery"></div>
<div class="tile t3" role="img" aria-label="Imported beer bottles"></div>
<div class="tile t4" role="img" aria-label="Grilled meat with tomatoes"></div>
<div class="tile t5" role="img" aria-label="Glasses of draft beer"></div>
<div class="tile t6" role="img" aria-label="Sliced grilled steak"></div>
<div class="tile t7" role="img" aria-label="Steak with cherry tomatoes"></div>
<div class="tile t8" role="img" aria-label="Beer bottles"></div>
<div class="abs beer-box">
  <h3>Imported beer<br>supplements</h3>
  <div class="price">$12</div>
  <div class="btn">View Details</div>
</div>

<!-- testimonials -->
<div class="abs testi" role="img" aria-label="Brushed silver tin background"></div>
<div class="photo plate plate-fries" role="img" aria-label="Plate of grilled chicken with potato wedges"></div>
<h2 class="abs script testi-script">Happy Customers</h2>
<h3 class="abs caps testi-title">Testimonials</h3>
<p class="quote" style="left:132px">Nemo enim ipsam voluptatem quia voluptas sit aspernatur aut odit aut fugit, sed quia consequuntur magni dolores eos qui ratione voluptatem sequi</p>
<p class="quote" style="left:453px">Nemo enim ipsam voluptatem quia voluptas sit aspernatur aut odit aut fugit, sed quia consequuntur magni dolores eos qui ratione voluptatem sequi</p>
<p class="quote" style="left:772px">Nemo enim ipsam voluptatem quia voluptas sit aspernatur aut odit aut fugit, sed quia consequuntur magni dolores eos qui ratione voluptatem sequi</p>
<div class="avatar" role="img" aria-label="Customer portrait" style="left:148px"></div>
<div class="avatar" role="img" aria-label="Customer portrait" style="left:470px"></div>
<div class="avatar" role="img" aria-label="Customer portrait" style="left:790px"></div>
<div class="who" style="left:256px">Sam Reed<br>Regular Guest</div>
<div class="who" style="left:578px">Lia Mora<br>Customer Business</div>
<div class="who" style="left:898px">Tom Vale<br>Weekend Regular</div>

<!-- footer -->
<div class="abs footer"></div>
<h4 class="f-head" style="left:135px">Take it easy with location</h4>
<p class="f-text" style="left:140px;top:3204px;width:290px">Nemo enim ipsam voluptatem quia voluptas sit aspernatur aut odit aut fugit, sed quia consequuntur magni dolores</p>
<p class="f-text" style="left:140px;top:3272px;width:290px">phone: 555 0142 8830<br>Email: hello@fizzshedgrill.example</p>
<div class="abs f-social"><span></span><span></span><span></span><span></span><span></span><span></span></div>

<h4 class="f-head" style="left:487px">Working Hours</h4>
<p class="f-text" style="left:440px;top:3190px;width:260px"><b>Monday To Friday</b><br><br>8:00am to 10:00pm(Breakfast)<br>11:00am to 10:00pm(Lunch/Dinner)<br><br><b>Saturday &amp; Sunday</b><br><br>10:00am to 11:00pm(Brunch)<br>11:00am to 12:00pm(Lunch/Dinner)</p>

<h4 class="f-head" style="left:765px">Feedback form</h4>
<div class="field" style="top:3158px">Name</div>
<div class="field" style="top:3202px">Email</div>
<div class="field" style="top:3246px">Phone</div>
<div class="field" style="top:3290px;height:80px">Message</div>
<div class="btn submit">Submit</div>

<div class="abs copyright">Copyright © 2016 Fizz's Shed and Grill</div>

</body>
</html>
```